Need A Standard Musical Download Website

We are looking for a talented designer to create a unique web design for our startup Music website called Vorde Sound.
The website should be responsive and filled with some creative stuffs along with bright colors.

Vorde sound is a website loaded with different types of music and capable of downloading the requested music by its users.
There will be categories of music which would be sorted by the genre. They include RnB, Hip-Hop, Afro pop, Pop, Dancehall and Reggae).

DESIGN STYLE/THEME

Creative, trendy, colorful, unique, and easy to use. You have freedom of selecting which ever color suits you. The design must be energetic and attractive.

NAVIGATION

HOME-MUSIC(RnB, Hip hop, Afro pop, POP, dancehall, Reggae)-ARTISTE-NEWS-LOGIN

PAGES REQUIRED
------------
1)Home Page
2)Music

FONTS
GOOGLE FONTS is strongly recommended.

Designers can get inspiration from https://tunabrook.example

Industry/Entity Type

Startup

```html
<!DOCTYPE html>
<html lang="en">
<head>
<meta charset="utf-8">
<title>Vorde Sound</title>
<link href="https://fonts.googleapis.com/css2?family=Open+Sans:wght@400;600;700;800&family=Raleway:wght@600;700&display=swap" rel="stylesheet">
<style>
:root{
  --red:#ea2c2e;
  --dark:#333;
  --grey:#777;
  --line:#ddd;
  --white:#fff;
}
*{box-sizing:border-box;margin:0;padding:0}
html,body{width:801px;height:1200px;overflow:hidden;background:var(--white);font-family:"Open Sans",sans-serif;color:var(--dark)}
.page{position:relative;width:801px;height:1200px;border-top:2px solid var(--red)}
.abs{position:absolute}
.brand{left:65px;top:16px;display:flex;align-items:center;gap:8px}
.brand-mark{width:26px;height:26px;background:var(--dark);border-radius:50%}
.brand-name{font-weight:700;font-size:17px;color:var(--dark)}
.auth{top:16px;height:28px;border:1px solid #bbb;border-radius:14px;color:var(--red);font-weight:600;font-size:11px;display:flex;align-items:center;justify-content:center;gap:5px}
.auth svg{width:9px;height:9px}
.nav{top:59px;left:0;width:801px;height:34px;border-top:1px solid var(--line)}
.nav a{position:absolute;top:11px;font-size:10px;font-weight:600;color:var(--dark);text-decoration:none}
.nav a.active{color:var(--red)}
.search{left:414px;top:0;width:321px;height:33px;border-left:1px solid var(--line);border-right:1px solid var(--line);font-size:10px;color:#888;padding:10px 12px}
.search svg{position:absolute;right:10px;top:10px;width:12px;height:12px}
.hero{left:0;top:93px;width:510px;height:308px;background:linear-gradient(135deg,#2b2b33,#5a3a40 40%,#2a2c3a 70%,#4a3a2e)}
.hero-title{left:0;top:68px;width:510px;text-align:center;color:var(--white);font-weight:800;font-size:38px;text-shadow:0 2px 4px rgba(0,0,0,.5)}
.hero-text{left:30px;top:120px;width:450px;text-align:center;color:var(--white);font-size:15px;line-height:24px;text-shadow:0 1px 3px rgba(0,0,0,.6)}
.hero-btn{left:156px;top:190px;width:195px;height:42px;background:var(--red);border:2px solid var(--white);border-radius:21px;color:var(--white);text-align:center;font-size:10px;line-height:13px;padding-top:7px}
.hero-btn b{font-size:11.5px;letter-spacing:.4px}
.trial{left:512px;top:93px;width:289px;height:308px;background:var(--red);color:var(--white)}
.trial h2{position:absolute;top:16px;width:100%;text-align:center;font-size:18px;font-weight:700}
.field{position:absolute;left:30px;width:234px;height:21px;background:var(--white);color:#555;font-size:8.5px;padding:5px 10px}
.field svg{position:absolute;right:10px;top:8px}
.check{left:30px;top:165px;font-size:8.5px;display:flex;align-items:center;gap:6px}
.check i{width:10px;height:10px;background:var(--white)}
.meta{left:30px;font-size:7.5px;display:flex;align-items:center;gap:4px}
.trial-btn{left:141px;top:190px;width:124px;height:33px;border:2px solid var(--white);border-radius:17px;font-size:10.5px;font-weight:700;text-align:center;line-height:29px}
.rule{left:30px;top:238px;width:234px;height:1px;background:rgba(255,255,255,.6)}
.badge{top:258px;height:27px;background:#111;border:1px solid var(--white);border-radius:4px}
.features{left:0;top:403px;width:801px;height:146px;display:flex;gap:2px}
.feature{flex:1;border:1px solid #e6e6e6;background:linear-gradient(#f2f2f2,#fff);text-align:center;padding-top:18px}
.feature svg{width:24px;height:24px}
.feature h3{font-family:"Raleway",sans-serif;font-size:13.5px;font-weight:700;margin-top:6px;color:#333}
.feature p{font-size:8px;color:var(--grey);line-height:14px;margin-top:6px}
.feature a{display:block;font-size:8px;font-weight:700;color:var(--red);margin-top:8px;text-decoration:none}
.cat-title{left:0;top:586px;width:801px;text-align:center;font-family:"Raleway",sans-serif;font-weight:700;font-size:19px}
.grid{left:66px;top:650px;width:669px;display:grid;grid-template-columns:repeat(3,221px);grid-auto-rows:168px;gap:3px 3px}
.tile{position:relative}
.t1{background:linear-gradient(135deg,#c88a4e,#7a5436 50%,#b6b0a4)}
.t2{background:#d62e30;display:flex;flex-direction:column;align-items:center;justify-content:center;color:var(--white)}
.t2 span{font-family:"Raleway",sans-serif;font-weight:700;font-size:19px;margin-top:6px}
.t3{background:linear-gradient(135deg,#6a4a2e,#a07048 50%,#2e2430)}
.t4{background:linear-gradient(90deg,#3c2c28,#c84a30 60%,#e0a040)}
.t5{background:linear-gradient(#4a1a1c,#7a2a24 60%,#8a5a30)}
.t6{background:linear-gradient(135deg,#1c1c18,#5a4a28 50%,#c8a830)}
.footer-line{left:0;top:1034px;width:801px;height:2px;background:var(--red)}
.social{left:300px;top:1068px;display:flex;gap:6px}
.social i{width:28px;height:28px;border:1px solid var(--red);border-radius:50%}
.links{left:0;width:801px;text-align:center;font-size:9px;color:#555}
.links span{margin:0 5px;color:#999}
.copy{left:0;top:1157px;width:801px;text-align:center;font-size:8.5px;color:#555}
</style>
</head>
<body>
<div class="page">
  <div class="abs brand"><i class="brand-mark"></i><span class="brand-name">VORDE SOUND</span></div>
  <div class="abs auth" style="left:582px;width:70px">
    <svg viewBox="0 0 10 10"><rect x="1" y="4" width="8" height="6" fill="#ea2c2e"/><path d="M3 4V3a2 2 0 0 1 4 0v1" stroke="#ea2c2e" fill="none" stroke-width="1.4"/></svg>LOGIN</div>
  <div class="abs auth" style="left:659px;width:77px">
    <svg viewBox="0 0 10 10"><path d="M1 9l1-3 5-5 2 2-5 5z" fill="#ea2c2e"/></svg>SIGNUP</div>

  <nav class="abs nav">
    <a class="active" style="left:66px">HOME</a>
    <a style="left:143px">MUSIC</a>
    <a style="left:224px">ARTISTE</a>
    <a style="left:312px">NEWS</a>
    <div class="abs search">Search free music to stream and download
      <svg viewBox="0 0 12 12"><circle cx="5" cy="5" r="4" stroke="#aaa" stroke-width="1.5" fill="none"/><path d="M8 8l3 3" stroke="#aaa" stroke-width="1.5"/></svg></div>
  </nav>

  <div class="abs hero" role="img" aria-label="Collage of live music photos: drummer, painted singer, vocalist at microphone, turntable, drumsticks and band">
    <div class="abs hero-title">VORDE SOUND</div>
    <p class="abs hero-text">Vorde sound is a website loaded with different types of music and capable of downloading the requested music by its users.</p>
    <div class="abs hero-btn">Download up to<br><b>30 FREE SONGS* WITH TRIAL</b></div>
  </div>

  <section class="abs trial">
    <h2>START YOUR TRIAL</h2>
    <div class="field" style="top:50px">Email Address</div>
    <div class="field" style="top:79px">Password</div>
    <div class="field" style="top:107px">Re-Enter Password</div>
    <div class="field" style="top:136px">Country<svg width="7" height="4" viewBox="0 0 7 4"><path d="M0 0h7L3.5 4z" fill="#aaa"/></svg></div>
    <div class="abs check"><i></i>Email me about new &amp; Free Music</div>
    <div class="abs meta" style="top:195px"><svg width="7" height="8" viewBox="0 0 7 8"><rect x=".5" y=".5" width="6" height="7" stroke="#fff" fill="none"/></svg>Terms &amp; Conditions</div>
    <div class="abs meta" style="top:211px"><svg width="7" height="8" viewBox="0 0 7 8"><rect y="3.5" width="7" height="4.5" fill="#fff"/><path d="M1.8 3.5V2.3a1.7 1.7 0 0 1 3.4 0v1.2" stroke="#fff" fill="none"/></svg>Secure Server</div>
    <div class="abs trial-btn">START YOUR TRIAL</div>
    <div class="abs rule"></div>
    <div class="abs badge" style="left:23px;width:76px"></div>
    <div class="abs badge" style="left:107px;width:78px"></div>
    <div class="abs badge" style="left:193px;width:78px"></div>
  </section>

  <div class="abs features">
    <div class="feature">
      <svg viewBox="0 0 24 24"><path d="M2 2h7L6.5 4.5 10 8 8 10 4.5 6.5 2 9zM22 2v7l-2.5-2.5L16 10l-2-2 3.5-3.5L15 2zM2 22v-7l2.5 2.5L8 14l2 2-3.5 3.5L9 22zM22 22h-7l2.5-2.5L14 16l2-2 3.5 3.5L22 15z" fill="#ea2c2e"/></svg>
      <h3>Expand Your Collections</h3>
      <p>At vero eos et accusamus et iusto odio<br>dignissimos ducimus qui blan</p>
      <a>READ MORE &gt;&gt;</a>
    </div>
    <div class="feature">
      <svg viewBox="0 0 24 24"><circle cx="10" cy="10" r="7" stroke="#ea2c2e" stroke-width="3" fill="none"/><path d="M15 15l7 7" stroke="#ea2c2e" stroke-width="3.5"/></svg>
      <h3>Discover More Music</h3>
      <p>At vero eos et accusamus et iusto odio<br>dignissimos ducimus qui blan</p>
      <a>EXPLORE MUSIC &gt;&gt;</a>
    </div>
    <div class="feature">
      <svg viewBox="0 0 24 24"><path d="M8 4l13-3v15" stroke="#ea2c2e" stroke-width="2.5" fill="none"/><path d="M8 4v15" stroke="#ea2c2e" stroke-width="2.5"/><ellipse cx="5" cy="19.5" rx="3.5" ry="2.8" fill="#ea2c2e"/><ellipse cx="18" cy="16.5" rx="3.5" ry="2.8" fill="#ea2c2e"/></svg>
      <h3>Unlimited Music</h3>
      <p>At vero eos et accusamus et iusto odio<br>dignissimos ducimus qui blan</p>
      <a>SEE OUR PRICING PLAN &gt;&gt;</a>
    </div>
    <div class="feature">
      <svg viewBox="0 0 24 24"><path d="M2 2h7L6.5 4.5 10 8 8 10 4.5 6.5 2 9zM22 2v7l-2.5-2.5L16 10l-2-2 3.5-3.5L15 2zM2 22v-7l2.5 2.5L8 14l2 2-3.5 3.5L9 22zM22 22h-7l2.5-2.5L14 16l2-2 3.5 3.5L22 15z" fill="#ea2c2e"/></svg>
      <h3>Membership</h3>
      <p>At vero eos et accusamus et iusto odio<br>dignissimos ducimus qui blan</p>
      <a>JOIN US NOW &gt;&gt;</a>
    </div>
  </div>

  <h2 class="abs cat-title">MUSIC CATEGORIES</h2>
  <div class="abs grid">
    <div class="tile t1" role="img" aria-label="Close-up of an acoustic guitar neck and strings"></div>
    <div class="tile t2" role="img" aria-label="Hip hop performer singing, under a red overlay">
      <svg width="76" height="60" viewBox="0 0 76 60"><path d="M10 40V32a28 28 0 0 1 56 0v8" stroke="#fff" stroke-width="5" fill="none"/><rect x="6" y="36" width="9" height="22" rx="4" fill="#fff"/><rect x="61" y="36" width="9" height="22" rx="4" fill="#fff"/><rect x="18" y="40" width="4" height="14" rx="2" fill="#fff"/><rect x="54" y="40" width="4" height="14" rx="2" fill="#fff"/></svg>
      <span>HIP POP MUSIC</span>
    </div>
    <div class="tile t3" role="img" aria-label="Singer performing on a warmly lit stage"></div>
    <div class="tile t4" role="img" aria-label="Vocalist singing into a microphone against colourful lights"></div>
    <div class="tile t5" role="img" aria-label="Traditional dancers and drummer on stage"></div>
    <div class="tile t6" role="img" aria-label="Hands playing a hand drum"></div>
  </div>

  <div class="abs footer-line"></div>
  <div class="abs social"><i></i><i></i><i></i><i></i><i></i><i></i></div>
  <p class="abs links" style="top:1110px">Home<span>|</span>About<span>|</span>Privacy Policy<span>|</span>Download Manager<span>|</span>Terms of Use<span>|</span>Start Your Trial<span>|</span>How it Works</p>
  <p class="abs links" style="top:1130px">Browse Selection<span>|</span>Why Join?<span>|</span>Affiliate Program<span>|</span>Gift Subscriptions</p>
  <p class="abs copy">Copyright © 2017, Vorde Sound. All right reserved.</p>
</div>
</body>
</html>
```